Brightfield Works - ELectrical Contractor Van Wrap

Looking for a new, modernized logo for our new van fleet. (2023 Varko Hauler Full Size)
Brightfield Works is an electrical contractor in Seattle, focusing on Commercial Electrical, Fire & Security installation, service & inspections. We would like to stick with white/black/grey/red as the color scheme. I added our logo & an image of our current small vans. I do not want them to match perfectly, but be similar. I am not opposed to getting rid of the Flame/Red Circle
Updates

Target Market(s)

Commercial Property Management groups/ Apartment Properties

Industry/Entity Type

Electrical

Colors
EB3D1F
EC4F4E
F09395
F8D3D4
FCEDEE

Requirements
Nice to have
• Modern/simplistic

```html
<!DOCTYPE html>
<html lang="en">
<head>
<meta charset="utf-8">
<title>Brightfield Works – Van Wrap Layouts</title>
<link rel="stylesheet" href="https://fonts.googleapis.com/css2?family=Oswald:wght@300;500&family=Poppins:wght@500;600;700&display=swap">
<style>
  :root {
    --wrap-red: #e41e26;
    --wrap-white: #f6f6f6;
    --band-dark: #3a3b3d;
    --text-grey: #4a4a4a;
    --outline: #c9cbce;
    --page: #ffffff;
  }
  html, body {
    margin: 0;
    width: 1200px;
    height: 1200px;
    overflow: hidden;
    background: var(--page);
  }
  .sheet {
    width: 1200px;
    height: 1200px;
    display: flex;
    flex-direction: column;
    justify-content: space-around;
    align-items: center;
    padding: 40px 0;
    box-sizing: border-box;
  }
  .wrap-panel { width: 1120px; height: 480px; display: block; }
  .body-red { fill: var(--wrap-red); }
  .body-white { fill: var(--wrap-white); }
  .body-outline { fill: none; stroke: var(--outline); stroke-width: 2; }
  .lower-band { fill: var(--band-dark); }
  .emblem-disc { fill: var(--wrap-red); stroke: var(--wrap-white); stroke-width: 12; }
  .wordmark-light {
    font-family: "Oswald", sans-serif;
    font-weight: 300;
    fill: var(--text-grey);
    font-size: 60px;
  }
  .wordmark-bold {
    font-family: "Oswald", sans-serif;
    font-weight: 500;
    fill: var(--text-grey);
    font-size: 60px;
    letter-spacing: 1px;
  }
  .tagline {
    font-family: "Poppins", sans-serif;
    font-weight: 500;
    fill: var(--text-grey);
    font-size: 18px;
    letter-spacing: 0.5px;
  }
  .phone-red {
    font-family: "Poppins", sans-serif;
    font-weight: 700;
    fill: var(--wrap-red);
    font-size: 38px;
    letter-spacing: 1px;
  }
  .contact-white {
    font-family: "Poppins", sans-serif;
    font-weight: 500;
    fill: #ffffff;
    font-size: 19px;
    letter-spacing: 1px;
  }
  .phone-white {
    font-family: "Poppins", sans-serif;
    font-weight: 700;
    fill: #ffffff;
    font-size: 27px;
    letter-spacing: 1px;
  }
  .services-strip {
    font-family: "Poppins", sans-serif;
    font-weight: 600;
    fill: #ffffff;
    font-size: 15px;
  }
  .services-red {
    font-family: "Poppins", sans-serif;
    font-weight: 700;
    fill: var(--wrap-red);
    font-size: 18px;
  }
  .sep-red { fill: var(--wrap-red); }
  .sep-grey { fill: var(--text-grey); }
</style>
</head>
<body>
<main class="sheet">

  <svg class="wrap-panel" viewBox="0 0 1120 480" aria-label="Van side wrap, layout A">
    <defs>
      <clipPath id="body-a">
        <path d="M30,330 L30,230 Q40,180 150,165 L290,70 Q320,40 400,40 L1060,40 Q1095,40 1095,80 L1095,420 L30,420 Z"/>
      </clipPath>
    </defs>
    <g clip-path="url(#body-a)">
      <rect class="body-white" x="0" y="0" width="1120" height="480"/>
      <rect class="body-red" x="0" y="0" width="560" height="480"/>
      <rect class="lower-band" x="0" y="345" width="1120" height="80"/>
    </g>
    <path class="body-outline" d="M30,330 L30,230 Q40,180 150,165 L290,70 Q320,40 400,40 L1060,40 Q1095,40 1095,80 L1095,420 L30,420 Z"/>
    <circle class="emblem-disc" cx="560" cy="192" r="140"/>

    <text class="wordmark-light" x="730" y="112">BRIGHTFIELD</text>
    <text class="wordmark-bold" x="730" y="180">WORKS</text>
    <text class="tagline" x="730" y="212">ELECTRICAL | FIRE | SECURITY</text>
    <text class="phone-red" x="730" y="290">555.014.2290</text>

    <text class="contact-white" x="170" y="305">BFW-ESE.COM</text>

    <text class="services-strip" x="560" y="392" text-anchor="middle">Commercial <tspan class="sep-red">•</tspan> Design <tspan class="sep-red">•</tspan> Installation <tspan class="sep-red">•</tspan> Service <tspan class="sep-red">•</tspan> Inspection</text>
  </svg>

  <svg class="wrap-panel" viewBox="0 0 1120 480" aria-label="Van side wrap, layout B">
    <defs>
      <clipPath id="body-b">
        <path d="M30,330 L30,230 Q40,180 150,165 L290,70 Q320,40 400,40 L1060,40 Q1095,40 1095,80 L1095,420 L30,420 Z"/>
      </clipPath>
    </defs>
    <g clip-path="url(#body-b)">
      <rect class="body-white" x="0" y="0" width="1120" height="480"/>
      <rect class="body-red" x="0" y="0" width="560" height="480"/>
      <rect class="lower-band" x="0" y="345" width="1120" height="80"/>
    </g>
    <path class="body-outline" d="M30,330 L30,230 Q40,180 150,165 L290,70 Q320,40 400,40 L1060,40 Q1095,40 1095,80 L1095,420 L30,420 Z"/>
    <circle class="emblem-disc" cx="560" cy="192" r="140"/>

    <text class="wordmark-light" x="730" y="112">BRIGHTFIELD</text>
    <text class="wordmark-bold" x="730" y="180">WORKS</text>
    <text class="tagline" x="730" y="212">ELECTRICAL | FIRE | SECURITY</text>

    <text class="phone-white" x="170" y="290">555.014.2290</text>
    <text class="contact-white" x="170" y="318">BFW-ESE.COM</text>

    <text class="services-red" x="900" y="268" text-anchor="middle">Commercial <tspan class="sep-grey">●</tspan> Design</text>
    <text class="services-red" x="900" y="296" text-anchor="middle">Installation <tspan class="sep-grey">●</tspan> Service <tspan class="sep-grey">●</tspan> Inspection</text>
  </svg>

</main>
</body>
</html>
```